Specialised investor in e-mobility and energy wants business card design

We need a business card design that fits our existing corporate design. <The look and feel must be 'sharp'/'clean', dynamic, communicate momentum, professionalism etc (as one would imagine from a firm in the financial sector). We like the idea of a reverse-side of the card that includes the logo, and the name and contact details on the other. We expect the deliverable to be whatever format might be required to be able to get cards printed directly by a service such as kelmo press. Our website is www.zub.capital

```html
<!DOCTYPE html>
<html lang="en">
<head>
<meta charset="utf-8">
<title>ZUB Capital – Business Card</title>
<link href="https://fonts.googleapis.com/css2?family=Lato:wght@400;700&family=Montserrat:wght@700&family=Questrial&display=swap" rel="stylesheet">
<style>
  :root {
    --backdrop: #1c1c1c;
    --card-white: #ffffff;
    --forest: #2f4f22;
    --leaf: #8ab44a;
    --on-forest: #ffffff;
  }
  * { box-sizing: border-box; margin: 0; padding: 0; }
  html, body { width: 1200px; height: 1122px; overflow: hidden; }
  body {
    background: var(--backdrop);
    position: relative;
    font-family: "Lato", sans-serif;
  }
  .card {
    position: absolute;
    width: 620px;
    height: 354px;
    border-radius: 22px;
    overflow: hidden;
    background: var(--card-white);
  }
  .card--front { left: 290px; top: 150px; }
  .card--back  { left: 290px; top: 610px; }

  .brand {
    display: flex;
    align-items: center;
    gap: 14px;
    font-family: "Questrial", sans-serif;
    font-weight: 400;
    white-space: nowrap;
  }
  .brand__dot { border-radius: 50%; flex: none; }

  .card--front .brand {
    position: absolute;
    inset: 0;
    justify-content: center;
    color: var(--forest);
    font-size: 74px;
  }
  .card--front .brand__dot { width: 22px; height: 22px; background: var(--leaf); }

  .card__waves { position: absolute; inset: 0; width: 620px; height: 354px; }

  .holder {
    position: absolute;
    right: 34px;
    top: 34px;
    text-align: right;
  }
  .holder__name {
    font-family: "Montserrat", sans-serif;
    font-weight: 700;
    font-size: 26px;
    color: var(--forest);
    letter-spacing: 0.5px;
  }
  .holder__role {
    font-size: 17px;
    color: var(--leaf);
    margin-top: 2px;
  }

  .card--back .brand {
    position: absolute;
    left: 56px;
    top: 258px;
    color: var(--on-forest);
    font-size: 42px;
    gap: 10px;
  }
  .card--back .brand__dot { width: 13px; height: 13px; background: var(--on-forest); }

  .divider {
    position: absolute;
    left: 352px;
    top: 188px;
    width: 1px;
    height: 134px;
    background: var(--leaf);
  }

  .contact {
    position: absolute;
    left: 374px;
    top: 184px;
    list-style: none;
    color: var(--on-forest);
    font-size: 15px;
    line-height: 1.4;
  }
  .contact li { display: flex; align-items: flex-start; gap: 10px; margin-bottom: 3px; }
  .contact svg { width: 13px; height: 13px; margin-top: 4px; flex: none; fill: var(--leaf); }
  .contact strong { font-weight: 700; }
</style>
</head>
<body>

  <section class="card card--front" aria-label="Card front">
    <div class="brand"><span class="brand__dot"></span>ZUB Capital</div>
  </section>

  <section class="card card--back" aria-label="Card back">
    <svg class="card__waves" viewBox="0 0 620 354" aria-hidden="true">
      <path d="M0,250 Q210,100 620,88 L620,108 Q240,112 0,268 Z" fill="var(--leaf)"/>
      <path d="M0,268 Q240,112 620,104 L620,354 L0,354 Z" fill="var(--forest)"/>
    </svg>

    <div class="holder">
      <div class="holder__name">MARK ELDING</div>
      <div class="holder__role">Founder &amp; CEO</div>
    </div>

    <div class="brand"><span class="brand__dot"></span>ZUB Capital</div>

    <div class="divider"></div>

    <ul class="contact">
      <li>
        <svg viewBox="0 0 24 24"><path d="M12 2a7 7 0 0 0-7 7c0 5 7 13 7 13s7-8 7-13a7 7 0 0 0-7-7zm0 9.5A2.5 2.5 0 1 1 12 6.5a2.5 2.5 0 0 1 0 5z"/></svg>
        <span><strong>ZUB Capital S.A.</strong><br>Harbour Row, Elmshire</span>
      </li>
      <li>
        <svg viewBox="0 0 24 24"><path d="M6.6 10.8a15 15 0 0 0 6.6 6.6l2.2-2.2a1 1 0 0 1 1-.25 11.4 11.4 0 0 0 3.6.6 1 1 0 0 1 1 1V20a1 1 0 0 1-1 1A17 17 0 0 1 3 4a1 1 0 0 1 1-1h3.5a1 1 0 0 1 1 1c0 1.25.2 2.45.6 3.6a1 1 0 0 1-.25 1z"/></svg>
        <span>+41 70418 2259</span>
      </li>
      <li>
        <svg viewBox="0 0 24 24"><path d="M2 5h20v14H2zm2 2v.5l8 5 8-5V7l-8 5z"/></svg>
        <span>mark@zub.capital</span>
      </li>
      <li>
        <svg viewBox="0 0 24 24"><path d="M12 2a10 10 0 1 0 0 20 10 10 0 0 0 0-20zm0 2a8 8 0 0 1 5.7 2.4H15l-2 2 1 2-2 1-1-1-3 1v2l2 2v3a8 8 0 0 1-6-7.7 8 8 0 0 1 8-8z"/></svg>
        <span>www.zub.capital</span>
      </li>
    </ul>
  </section>

</body>
</html>
```